Request for Business Card Design

Hi. My name is Marlene, I am looking for a new business card design for my company, Quarrow Signal Instruments, LLC. I really like the design you did for Tarsel Venture and was hoping you could do something similar using our full logo and our mark. I am also open to any raised texture design using our mark. I have attached our full logo, which would need to be somewhere on the card, as well as the mark in both outline and full form, as well as our brand colors / guide. The card does not have to be white, as long as our logo and mark appear. I actually like darker colored business cards more, but am open to all options. If you are interested in working with me, please let me know. We would also take the business card design into letterhead design if you can do that.

```html
<!DOCTYPE html>
<html lang="en">
<head>
<meta charset="utf-8">
<title>Quarrow Signal Instruments — Business Card</title>
<link href="https://fonts.googleapis.com/css2?family=Open+Sans:wght@400;700&family=Marcellus&display=swap" rel="stylesheet">
<style>
  :root {
    --stage: #3a3b3d;
    --card: #050607;
    --brand-blue: #1b9ac4;
    --deco-blue: #0b2530;
    --ink: #f2f4f5;
    --rule: #3b4a50;
  }
  * { margin: 0; padding: 0; box-sizing: border-box; }
  html, body { width: 1200px; height: 900px; overflow: hidden; background: var(--stage); }
  .stage { position: relative; width: 1200px; height: 900px; }
  .card {
    position: absolute; left: 250px; width: 700px; height: 400px;
    background: var(--card); border-radius: 26px; overflow: hidden;
    box-shadow: 0 18px 40px rgba(0,0,0,.45);
    font-family: "Open Sans", sans-serif; color: var(--ink);
  }
  .card--back { top: 38px; }
  .card--front { top: 466px; }

  /* back */
  .back-brand {
    position: absolute; left: 0; right: 0; top: 130px; text-align: center;
  }
  .brand-name { font-weight: 700; color: var(--ink); letter-spacing: 2px; line-height: 1; }
  .back-brand .brand-name { font-size: 40px; }
  .back-brand .brand-sub { font-size: 13px; margin-top: 8px; letter-spacing: 3px; }
  .back-rule {
    position: absolute; left: 150px; right: 150px; top: 250px; height: 1px;
    background: linear-gradient(90deg, transparent, var(--brand-blue), transparent);
  }
  .back-web {
    position: absolute; left: 0; right: 0; top: 268px; text-align: center;
    font-family: "Marcellus", serif; font-size: 17px; letter-spacing: 6px;
  }
  .back-web .accent { color: var(--brand-blue); }

  /* front */
  .deco-disc {
    position: absolute; left: 120px; top: 170px; width: 360px; height: 360px;
    border-radius: 50%; background: var(--deco-blue);
  }
  .front-brand { position: absolute; left: 44px; top: 42px; display: flex; align-items: center; gap: 16px; }
  .brand-dot { width: 46px; height: 46px; border-radius: 50%; background: var(--brand-blue); }
  .front-brand .brand-name { font-size: 44px; }
  .front-brand .brand-sub { font-size: 13px; margin-top: 4px; letter-spacing: 1px; }

  .person { position: absolute; right: 300px; top: 250px; text-align: right; font-family: "Marcellus", serif; }
  .person-title { font-size: 15px; letter-spacing: 1px; }
  .person-name { font-size: 20px; color: var(--brand-blue); margin-top: 4px; letter-spacing: 1px; }

  .divider { position: absolute; left: 420px; top: 200px; width: 1px; height: 130px; background: var(--rule); }

  .contacts { position: absolute; left: 440px; top: 202px; list-style: none; font-size: 13px; line-height: 1.55; }
  .contacts li { display: flex; align-items: flex-start; gap: 9px; }
  .contacts svg { width: 13px; height: 13px; margin-top: 3px; flex: none; fill: var(--brand-blue); }
</style>
</head>
<body>
<main class="stage">

  <section class="card card--back" aria-label="Card back">
    <div class="back-brand">
      <div class="brand-name">QUARROW</div>
      <div class="brand-name brand-sub">SIGNAL INSTRUMENTS</div>
    </div>
    <div class="back-rule"></div>
    <p class="back-web">www.<span class="accent">quarrowsignal</span>.com</p>
  </section>

  <section class="card card--front" aria-label="Card front">
    <div class="deco-disc"></div>
    <div class="front-brand">
      <div class="brand-dot"></div>
      <div>
        <div class="brand-name">QUARROW</div>
        <div class="brand-name brand-sub">SIGNAL INSTRUMENTS</div>
      </div>
    </div>

    <div class="person">
      <p class="person-title">PRESIDENT &amp; CEO</p>
      <p class="person-name">DR. ALDEN WHITCOMBE</p>
    </div>

    <div class="divider"></div>

    <ul class="contacts">
      <li><svg viewBox="0 0 16 16"><path d="M3 1l3 3-2 2c1 2 3 4 5 5l2-2 3 3-2 3C6 14 2 10 1 3z"/></svg>+001 555 210 4837</li>
      <li><svg viewBox="0 0 16 16"><rect x="4" y="1" width="8" height="4"/><rect x="1" y="6" width="14" height="6" rx="1"/><rect x="4" y="10" width="8" height="5"/></svg>+001 555 210 4890</li>
      <li><svg viewBox="0 0 16 16"><path d="M1 3h14v10H1z M2 4l6 5 6-5" fill="none" stroke="#1b9ac4" stroke-width="1.6"/></svg>info@quarrowsignal.com</li>
      <li><svg viewBox="0 0 16 16"><circle cx="8" cy="8" r="6.5" fill="none" stroke="#1b9ac4" stroke-width="1.4"/><path d="M1.5 8h13M8 1.5c-3 3-3 10 0 13M8 1.5c3 3 3 10 0 13" fill="none" stroke="#1b9ac4" stroke-width="1.2"/></svg>www.quarrowsignal.com</li>
      <li><svg viewBox="0 0 16 16"><path d="M8 0a5 5 0 0 1 5 5c0 4-5 11-5 11S3 9 3 5a5 5 0 0 1 5-5zm0 3a2 2 0 1 0 0 4 2 2 0 0 0 0-4z"/></svg>118 Meridian Works Road<br>Harlow Falls, CO 80999</li>
    </ul>
  </section>

</main>
</body>
</html>
```